Brook Refrigeration. Refrigeration and air conditioning specialists.

We need a website to promote our business. We would a modern simple design using the colours from our logo and black. We want it to be fun but proffesional.

Target Market(s)

Commercial

Number of Pages Required

4 page

Requirements
Must have
• Home Page, About Us, Services and Contact Us.
• 24/7 365 days service available.
• Brook Refrigeration's dedicated team specialises in commercial refrigeration and air conditioning equipment.
• Based in Kestrel Bay, we cover Westhaven Metro and surrounding areas.
Nice to have
• KNOWLEDGE . EXPERIENCE . PASSION in bold.
• Our experienced and highly trained technicians provide extensive knowledge and exceptional skills for your commercial refrigeration and air conditioning requirements.
• Pictures of commercial refrigeration.
Should not have
• No mention of domestic services.

```html
<!DOCTYPE html>
<html lang="en">
<head>
<meta charset="utf-8">
<title>Brook Refrigeration</title>
<link rel="stylesheet" href="https://fonts.googleapis.com/css2?family=Montserrat:wght@400;500;600;700&family=Roboto+Condensed:wght@400;700&family=Roboto:wght@300;400;500;700&display=swap">
<style>
:root{
  --purple:#3b2462;
  --purple-dark:#2f1c50;
  --green:#a6ef6d;
  --green-deep:#8fdc55;
  --ink:#2a2a2a;
  --grey-text:#5b5b5b;
  --footer:#333333;
  --white:#ffffff;
  --line:#c9c9c9;
}
*{box-sizing:border-box;margin:0;padding:0}
html,body{width:1200px;height:3383px;overflow:hidden}
body{position:relative;background:var(--white);font-family:"Roboto",Arial,sans-serif;color:var(--ink)}

/* Header */
.site-header{position:absolute;left:0;top:0;width:1200px;height:138px;background:var(--white)}
.brand{position:absolute;left:122px;top:40px;width:200px;font-family:"Montserrat",sans-serif;font-weight:700;color:var(--green);font-size:40px;line-height:40px;letter-spacing:1px}
.brand small{display:block;font-size:13px;line-height:18px;letter-spacing:1px}
.header-phone{position:absolute;left:638px;top:32px;font-family:"Roboto",sans-serif;font-weight:700;font-size:21px;color:var(--purple);display:flex;align-items:center;gap:10px}
.social{position:absolute;left:864px;top:34px;display:flex;gap:3px}
.social span{width:21px;height:21px;background:var(--purple);display:block}
.badge{position:absolute;left:1005px;top:14px;width:120px;text-align:center;font-family:"Roboto Condensed",sans-serif;color:var(--purple)}
.badge .dot{width:32px;height:32px;border-radius:50%;border:3px solid var(--purple);margin:0 auto 2px}
.badge b{font-size:20px}
.badge em{font-style:normal;font-size:11px;font-weight:700}
.badge i{display:block;font-style:normal;font-size:7px;letter-spacing:.5px}
.main-nav{position:absolute;left:475px;top:90px;width:725px;height:42px}
.main-nav svg{position:absolute;left:0;top:0}
.main-nav ul{position:absolute;left:0;top:0;width:725px;height:42px;list-style:none;font-family:"Montserrat",sans-serif;font-size:15px;color:var(--white)}
.main-nav li{position:absolute;top:12px;white-space:nowrap}
.main-nav li.active{color:var(--green);font-weight:700}
.header-rule{position:absolute;left:0;top:131px;width:1200px;height:6px;background:var(--green)}

/* Hero */
.hero{position:absolute;left:0;top:137px;width:1200px;height:701px}
.hero-photo{position:absolute;inset:0;background:linear-gradient(180deg,#8c949a 0%,#6f767b 40%,#4d5357 100%)}
.hero-shade{position:absolute;inset:0;background:rgba(20,20,25,.35)}
.hero-copy{position:absolute;left:0;width:1200px;text-align:center;color:var(--white)}
.hero-intro{top:198px;font-family:"Montserrat",sans-serif;font-weight:400;font-size:40px}
.hero-title{top:254px;font-family:"Roboto Condensed",sans-serif;font-weight:700;font-size:56px;line-height:72px;text-transform:uppercase}
.hero-values{top:395px;font-family:"Roboto Condensed",sans-serif;font-weight:700;font-size:46px;color:var(--green);letter-spacing:1px}
.hero-btn{position:absolute;left:514px;top:485px;width:192px;height:42px;background:var(--green);border-radius:6px;font-family:"Roboto Condensed",sans-serif;font-size:23px;color:var(--ink);text-align:center;line-height:42px}
.hero-dots{position:absolute;left:578px;top:645px;display:flex;gap:10px}
.hero-dots span{width:10px;height:10px;border-radius:50%;border:2px solid var(--white)}
.hero-dots span.on{background:var(--white)}

/* Section headings */
.section-title{position:absolute;left:0;width:1200px;text-align:center;font-family:"Montserrat",sans-serif;font-weight:500;font-size:34px}
.title-rule{position:absolute;left:563px;width:74px;height:2px;background:#b9b9c9}

/* About */
.about-title{top:934px;color:var(--purple)}
.about-rule{top:985px}
.about-intro{position:absolute;left:0;top:1012px;width:1200px;text-align:center;font-size:13px;line-height:23px;color:var(--grey-text)}
.about-photo{position:absolute;left:124px;top:1099px;width:456px;height:282px;background:linear-gradient(135deg,#6e7a62 0%,#9aa39a 50%,#c6c8c2 100%);border:1px solid #ddd}
.about-text{position:absolute;left:620px;top:1094px;width:485px;font-size:12.5px;line-height:22px;color:var(--grey-text);text-align:justify}
.about-text p+p{margin-top:18px}

/* Services */
.services{position:absolute;left:0;top:1498px;width:1200px;height:695px;background:var(--purple)}
.services-title{top:68px;color:var(--green)}
.services-intro{position:absolute;left:0;top:156px;width:1200px;text-align:center;font-size:13px;line-height:23px;color:#e6e0f0}
.service-arrow{position:absolute;top:328px}
.service-card{position:absolute;top:250px;width:254px;text-align:center}
.service-pic{width:228px;height:228px;margin:0 auto;border-radius:50%;border:5px solid var(--green);background:var(--white);display:flex;align-items:center;justify-content:center}
.service-pic span{display:block;width:150px;height:150px;border-radius:10px;background:linear-gradient(160deg,#e9ebee,#9ea4ab)}
.service-name{margin-top:20px;font-family:"Roboto",sans-serif;font-weight:500;font-size:17px;color:var(--green)}
.service-desc{margin:6px auto 0;width:200px;font-size:12.5px;line-height:17px;color:#e6e0f0}
.service-btn{display:inline-block;margin-top:14px;width:80px;height:24px;line-height:24px;background:var(--green);color:var(--ink);font-size:11px}

/* Contact */
.contact-title{top:2305px;color:var(--purple);font-family:"Roboto",sans-serif;font-weight:700}
.contact-rule{top:2360px}
.field-label{position:absolute;font-size:13.5px;color:var(--grey-text)}
.field-label b{color:var(--purple);font-weight:400;margin-left:6px}
.field{position:absolute;border:1px solid var(--line);background:var(--white)}
.required-note{position:absolute;left:675px;top:2584px;font-size:12.5px;color:var(--grey-text)}
.required-note b{color:var(--purple);font-weight:400}
.consent{position:absolute;left:675px;top:2622px;font-size:13px;color:var(--grey-text);display:flex;align-items:center;gap:12px}
.consent span{width:15px;height:15px;border:1px solid var(--line)}
.submit-btn{position:absolute;left:532px;top:2709px;width:136px;height:37px;background:var(--purple);color:var(--white);font-family:"Roboto",sans-serif;font-weight:500;font-size:17px;text-align:center;line-height:37px;border-radius:3px}

/* Newsletter */
.newsletter{position:absolute;left:0;top:2829px;width:1200px;height:149px;background:var(--green)}
.newsletter h3{position:absolute;left:174px;top:63px;font-family:"Roboto",sans-serif;font-weight:700;font-size:25px;color:var(--purple)}
.newsletter .news-field{position:absolute;left:384px;top:52px;width:503px;height:52px;background:var(--white)}
.newsletter .news-btn{position:absolute;left:887px;top:52px;width:128px;height:52px;background:var(--purple);color:var(--white);font-weight:700;font-size:13.5px;text-align:center;line-height:52px}

/* Footer */
.site-footer{position:absolute;left:0;top:2978px;width:1200px;height:322px;background:var(--footer);color:var(--white)}
.footer-brand{position:absolute;left:112px;top:108px;font-family:"Montserrat",sans-serif;font-weight:700;font-size:44px;line-height:44px;color:var(--white)}
.footer-brand small{display:block;font-size:14px;line-height:20px;letter-spacing:1px}
.footer-heading{position:absolute;top:70px;font-family:"Roboto",sans-serif;font-weight:700;font-size:16px;color:var(--green)}
.footer-item{position:absolute;left:359px;display:flex;gap:14px}
.footer-item h4{font-size:13.5px;color:var(--green);font-weight:700}
.footer-item p{font-size:14px;line-height:18px}
.footer-links{position:absolute;left:628px;top:119px;list-style:none;font-size:14px;line-height:34px}
.footer-input{position:absolute;height:38px;background:var(--white);color:#8a8a8a;font-size:13.5px;padding:10px 12px}
.footer-send{position:absolute;left:794px;top:208px;width:131px;height:36px;background:var(--green);color:var(--ink);font-weight:700;font-size:15px;text-align:center;line-height:36px}
.copyright{position:absolute;left:0;top:3300px;width:1200px;height:83px;background:var(--purple);color:#cfc7dd;text-align:center;font-size:12px;line-height:83px}
</style>
</head>
<body>

<header class="site-header">
  <div class="brand">Brook<small>Refrigeration</small></div>
  <div class="header-phone">
    <svg width="14" height="22" viewBox="0 0 14 22"><rect x="1.5" y="1.5" width="11" height="19" rx="2" fill="none" stroke="#3b2462" stroke-width="2.5"/><circle cx="7" cy="17" r="1.3" fill="#3b2462"/></svg>
    1-888-555-0142
  </div>
  <div class="social"><span></span><span></span><span></span><span></span></div>
  <div class="badge">
    <div class="dot"></div>
    <b>24/7</b> <em>365 DAYS</em>
    <i>SERVICE AVAILABLE</i>
  </div>
  <nav class="main-nav">
    <svg width="725" height="42"><polygon points="32,0 725,0 725,42 0,42" fill="#3b2462"/></svg>
    <ul>
      <li class="active" style="left:103px">HOME</li>
      <li style="left:247px">ABOUT US</li>
      <li style="left:405px">SERVICES</li>
      <li style="left:558px">CONTACT US</li>
    </ul>
  </nav>
  <div class="header-rule"></div>
</header>

<section class="hero">
  <div class="hero-photo" role="img" aria-label="Rows of commercial air conditioning condenser units under a cloudy sky"></div>
  <div class="hero-shade"></div>
  <p class="hero-copy hero-intro">Our dedicated team specialises in</p>
  <h1 class="hero-copy hero-title">Commercial Refrigeration &amp;<br>Air Conditioning Equipment.</h1>
  <p class="hero-copy hero-values">KNOWLEDGE • EXPERIENCE • PASSION</p>
  <div class="hero-btn">KNOW MORE</div>
  <div class="hero-dots"><span class="on"></span><span></span><span></span></div>
</section>

<section class="about">
  <h2 class="section-title about-title">About us</h2>
  <div class="title-rule about-rule"></div>
  <p class="about-intro">Brook Refrigeration's dedicated team specialises in commercial refrigeration and air conditioning equipment.<br>Based in Kestrel Bay, we cover Westhaven Metro and surrounding areas.</p>
  <div class="about-photo" role="img" aria-label="Technician testing a commercial refrigeration unit with a multimeter"></div>
  <div class="about-text">
    <p>Our experienced and highly trained technicians provide extensive knowledge and exceptional skills for your commercial refrigeration and air conditioning requirements. From cool rooms and freezers to display cabinets and split systems, we install, service and repair equipment for restaurants, cafes, supermarkets, hotels and warehouses. Every job is completed safely, on time and with care for your business.</p>
    <p>Breakdowns rarely happen at a convenient hour, which is why our team is on call 24 hours a day, 365 days a year. We carry common parts in our vans, explain the work clearly before we start and offer planned maintenance to keep your systems running efficiently.</p>
  </div>
</section>

<section class="services">
  <h2 class="section-title services-title">Our Services</h2>
  <p class="services-intro">Whether you wish to cool, store or display food and drink, we have a wide range of commercial refrigerator services catering to various small and large scale industries.<br>We specialize in wide range of commercial refrigeration operations and maintenance services to ensure efficient functioning of the systems:</p>
  <svg class="service-arrow" style="left:50px" width="26" height="50" viewBox="0 0 26 50"><polyline points="24,2 3,25 24,48" fill="none" stroke="#8e7fb0" stroke-width="2"/></svg>
  <svg class="service-arrow" style="left:1124px" width="26" height="50" viewBox="0 0 26 50"><polyline points="2,2 23,25 2,48" fill="none" stroke="#8e7fb0" stroke-width="2"/></svg>

  <div class="service-card" style="left:94px">
    <div class="service-pic"><span role="img" aria-label="Commercial chest freezer"></span></div>
    <h3 class="service-name">Commercial Freezer</h3>
    <p class="service-desc">Supply, installation and repair of chest freezers.</p>
    <span class="service-btn">Read more</span>
  </div>
  <div class="service-card" style="left:347px">
    <div class="service-pic"><span role="img" aria-label="Walk-in cool room"></span></div>
    <h3 class="service-name">Walk In Cooler</h3>
    <p class="service-desc">Custom cool rooms built and serviced on site.</p>
    <span class="service-btn">Read more</span>
  </div>
  <div class="service-card" style="left:602px">
    <div class="service-pic"><span role="img" aria-label="Stainless steel kitchen refrigerator"></span></div>
    <h3 class="service-name">Kitchen Refrigeration</h3>
    <p class="service-desc">Reach-in fridges and prep units for busy kitchens.</p>
    <span class="service-btn">Read more</span>
  </div>
  <div class="service-card" style="left:857px">
    <div class="service-pic"><span role="img" aria-label="Glass door display merchandiser fridge"></span></div>
    <h3 class="service-name">Glass Door Merchandiser</h3>
    <p class="service-desc">Bright, efficient display fridges for retail spaces.</p>
    <span class="service-btn">Read more</span>
  </div>
</section>

<section class="contact">
  <h2 class="section-title contact-title">Contact Us</h2>
  <div class="title-rule contact-rule"></div>
  <label class="field-label" style="left:151px;top:2416px">Name<b>*</b></label>
  <div class="field" style="left:151px;top:2441px;width:397px;height:36px"></div>
  <label class="field-label" style="left:151px;top:2500px">Email<b>*</b></label>
  <div class="field" style="left:151px;top:2524px;width:397px;height:37px"></div>
  <label class="field-label" style="left:151px;top:2586px">Phone</label>
  <div class="field" style="left:151px;top:2610px;width:397px;height:36px"></div>
  <label class="field-label" style="left:675px;top:2416px">Description</label>
  <div class="field" style="left:675px;top:2441px;width:395px;height:131px"></div>
  <p class="required-note"><b>*</b> Required</p>
  <div class="consent"><span></span>I have read the Disclaimer and Privacy Policy</div>
  <div class="submit-btn">SUBMIT</div>
</section>

<section class="newsletter">
  <h3>NEWSLETTER</h3>
  <div class="news-field"></div>
  <div class="news-btn">SUBSCRIBE</div>
</section>

<footer class="site-footer">
  <div class="footer-brand">Brook<small>Refrigeration</small></div>

  <h3 class="footer-heading" style="left:359px">CONTACT US</h3>
  <div class="footer-item" style="top:108px">
    <svg width="20" height="28" viewBox="0 0 20 28"><path d="M10 1C5 1 1.5 4.8 1.5 9.5 1.5 16 10 26 10 26s8.5-10 8.5-16.5C18.5 4.8 15 1 10 1z" fill="#a6ef6d"/><circle cx="10" cy="9.5" r="3.5" fill="#333"/></svg>
    <div><h4>ADDRESS</h4><p>12 Lakeside Drive<br>Kestrel Bay 4821</p></div>
  </div>
  <div class="footer-item" style="top:193px">
    <svg width="20" height="22" viewBox="0 0 20 22"><path d="M4 1l4 5-2.5 2.5c1.2 2.8 3.5 5.2 6.5 6.5L14.5 12.5l5 4-2.5 4C9 20 1 12 1 4z" fill="#a6ef6d"/></svg>
    <div><h4>PHONE NUMBER</h4><p>1-888-555-0142</p></div>
  </div>

  <h3 class="footer-heading" style="left:625px">ABOUT</h3>
  <ul class="footer-links"><li>Home</li><li>About Us</li><li>Services</li><li>Contact us</li></ul>

  <h3 class="footer-heading" style="left:790px">GET IN TOUCH</h3>
  <div class="footer-input" style="left:790px;top:108px;width:157px">Name</div>
  <div class="footer-input" style="left:952px;top:108px;width:153px">Phone</div>
  <div class="footer-input" style="left:790px;top:153px;width:315px">Email address</div>
  <div class="footer-send">SEND</div>
</footer>

<div class="copyright">© 2018 brookrefrigeration All Right Reserved</div>

</body>
</html>
```